Fresh, modern, fun business card for pediatric dental practice

Need a business card for fresh, modern, fun pediatric dental practice

Clean look that matches our website's font and colors

We prefer the look of curved corners on business cards

Target Market(s)

parents (mothers) of young children, professionals, mid-high class

Industry/Entity Type

Dental

Contact Information for Business Card

Maplebrook Pediatric Dentistry
482 Quarry Lane
Suite 517
Fernhollow, PA 17599
717.555.0193
www.maplebrookkidsdental.example

Mei-Ran Tsai, DMD
Corinne Walbeck, DMD
(we are working on our email address, but we would like that on the card as well)

Font styles to use
Sans Serif

Requirements
Must have
• All info; we would also like to make cards for individual staff members
• colors from our website and color palatte, attatched
• use same font and design as website for branding
Nice to have
• clean, simple card that has a pop of color
• we would like to see a few designs with our tag line "where smiles get brighter"
• we are not sure if we want to have it on there or not
• we would like to see a few designs incorporating the ribbon graphic on our website where the word WELCOME is

```html
<!DOCTYPE html>
<html lang="en">
<head>
<meta charset="utf-8">
<title>Maplebrook Pediatric Dentistry – Business Card</title>
<link rel="stylesheet" href="https://fonts.googleapis.com/css2?family=Open+Sans:wght@600&family=Roboto:wght@400&family=Roboto+Condensed:wght@500;700&display=swap">
<style>
  :root {
    --stage: #2b2b2b;
    --paper: #f4f4f4;
    --magenta: #c72e8c;
    --gold: #efb426;
    --white: #ffffff;
  }
  * { margin: 0; padding: 0; box-sizing: border-box; }
  html, body { width: 1200px; height: 960px; overflow: hidden; background: var(--stage); }
  .card {
    position: absolute;
    width: 600px;
    height: 342px;
    border-radius: 22px;
    overflow: hidden;
  }
  .card--front { left: 314px; top: 113px; background: var(--paper); }
  .card--back { left: 311px; top: 472px; background: var(--gold); }

  .wave { position: absolute; inset: 0; width: 600px; height: 342px; }

  .brand {
    position: absolute;
    left: 40px;
    top: 42px;
    color: var(--gold);
    font-family: "Open Sans", sans-serif;
    font-weight: 600;
  }
  .brand__dot {
    display: block;
    width: 34px; height: 34px;
    margin: 0 0 12px 92px;
    border-radius: 50%;
    background: var(--gold);
  }
  .brand__name { font-size: 34px; line-height: 36px; letter-spacing: 0.5px; }
  .brand__sub { font-size: 19px; line-height: 24px; }

  .contact {
    position: absolute;
    right: 29px;
    top: 132px;
    text-align: right;
    color: var(--white);
    font-family: "Roboto", sans-serif;
    font-size: 14px;
    line-height: 18px;
  }
  .contact__doctors {
    font-family: "Roboto Condensed", sans-serif;
    font-weight: 500;
    font-size: 21px;
    line-height: 24px;
    color: var(--gold);
    margin-bottom: 14px;
  }
  .contact__address { margin-bottom: 12px; }
  .contact__label {
    color: var(--gold);
    font-family: "Roboto Condensed", sans-serif;
    font-weight: 700;
    font-size: 15px;
  }

  .back-mark {
    position: absolute;
    left: 0; right: 0; top: 88px;
    text-align: center;
    color: var(--white);
    font-family: "Open Sans", sans-serif;
    font-weight: 600;
  }
  .back-mark__dot {
    display: block;
    width: 72px; height: 72px;
    margin: 0 auto 18px;
    border-radius: 50%;
    border: 10px solid var(--white);
  }
  .back-mark__name { font-size: 34px; line-height: 40px; }
  .back-url {
    position: absolute;
    left: 0; right: 0; top: 294px;
    text-align: center;
    color: var(--white);
    font-family: "Roboto", sans-serif;
    font-size: 13px;
    letter-spacing: 4px;
  }
</style>
</head>
<body>
  <section class="card card--front">
    <svg class="wave" viewBox="0 0 600 342" aria-hidden="true">
      <path d="M0,230 C60,262 110,288 160,285 C260,280 330,150 420,95 C480,60 540,47 600,47 L600,342 L0,342 Z" fill="var(--magenta)"/>
      <path d="M0,230 C60,262 110,288 160,285 C260,280 330,150 420,95 C480,60 540,47 600,47" fill="none" stroke="var(--white)" stroke-width="9"/>
      <path d="M0,226 C60,258 110,284 160,281 C260,276 330,146 420,91 C480,56 540,43 600,43" fill="none" stroke="var(--gold)" stroke-width="5"/>
    </svg>

    <div class="brand">
      <span class="brand__dot"></span>
      <div class="brand__name">Maplebrook</div>
      <div class="brand__sub">Pediatric Dentistry</div>
    </div>

    <div class="contact">
      <div class="contact__doctors">
        Mei-Ran Tsai, DMD<br>
        Corinne Walbeck, DMD
      </div>
      <div class="contact__address">
        Maplebrook Pediatric Dentistry<br>
        482 Quarry Lane<br>
        Suite 517<br>
        Fernhollow, PA 17599
      </div>
      <div><span class="contact__label">Phone:</span> 717.555.0193</div>
      <div><span class="contact__label">Web:</span> maplebrookkidsdental.example</div>
    </div>
  </section>

  <section class="card card--back">
    <div class="back-mark">
      <span class="back-mark__dot"></span>
      <div class="back-mark__name">Maplebrook</div>
    </div>
    <div class="back-url">www.maplebrookkidsdental.example</div>
  </section>
</body>
</html>
```